KVR Inc Web Design

WHAT ARE WE DOING?
We are developing a new website look and feel for a new company called KVR Inc. This new look and feel should include colors, design elements, choice of photography and other imagery, fonts, and other user experience elements.

WHAT DO THEY DO?
KVR, Inc, makes tools for researchers who are studying protein-protein interactions. These molecules are the basic tools of biology, and serve as key targets for drug developers and disease researchers. The world of proteins is enormously complex, and companies like KVR provide researchers with critical tools that help them elucidate this world.

WHO ARE WE TALKING TO?
The target audience for this website are professional scientists working in university research or biopharma drug development. They are highly sophisticated consumers looking for key tools that will advance their research.

WHAT DO WE WANT THEM TO DO?
The site is an information resource for the customer exploring the tools that KVR sells and the scientific issues surrounding protein-protein interactions. They should be able to navigate easily to their content of choice, while the whole site should convey a professionalism that enhanced KVR’s credibility.

WHAT DOES THE KVR BRAND STAND FOR?
KVR stands for illumination. Proteins are challenging to study, and KVR exists to help shed light on their workings.

WHAT ARE THE KEY VALUES OF THE KVR BRAND?
Integrity. Innovation. Insight.

WHAT ARE THE EXECUTIONAL MANDITORIES?
The look and feel is completely up for grabs. Nothing is off the table.

WHAT ARE THE DELIVERABLES?
We need new designs for the following templates:
http://cms.marlowbench.com/
http://cms.marlowbench.com/products-and-services/instruments-3/bench-top-instruments/
http://cms.marlowbench.com/category/lab-study/

```html
<!DOCTYPE html>
<html lang="en">
<head>
<meta charset="utf-8">
<title>KVR Inc – Pipettes</title>
<link href="https://fonts.googleapis.com/css2?family=Figtree:ital,wght@0,400;0,500;0,600;0,700;1,700&display=swap" rel="stylesheet">
<style>
:root{
  --orange:#f9b233;
  --blue:#33b5d9;
  --text:#666;
  --dark:#111;
  --line:#d6d6d6;
  --tab:#e3e2e3;
  --footer:#6b6b6b;
  --white:#fff;
}
*{box-sizing:border-box;margin:0;padding:0}
html,body{width:1169px;height:1200px;overflow:hidden;background:var(--white);font-family:"Figtree",Arial,sans-serif;color:var(--text)}
.page{position:relative;width:1169px;height:1200px}
.wrap{position:absolute;left:117px;width:936px}

.site-header{position:absolute;top:0;left:0;width:100%;height:60px;border-top:3px solid var(--orange);border-bottom:1px solid #e8e8e8;box-shadow:0 1px 3px rgba(0,0,0,.05)}
.brand{position:absolute;left:117px;top:14px;font-size:25px;font-weight:600;color:#6a6a6a;line-height:30px}
.main-nav{position:absolute;left:297px;top:19px;display:flex;gap:22px;font-size:15.5px;font-weight:600;color:#666}
.main-nav .active{color:var(--orange)}
.search{position:absolute;left:918px;top:18px;width:134px;height:25px;background:linear-gradient(#8a8a8a,#6f6f6f);border-radius:2px;color:#ddd;font-size:12.5px;padding:5px 7px}
.search svg{position:absolute;right:6px;top:6px}

.page-title{top:90px;height:40px;border-bottom:3px double var(--line)}
.page-title h1{font-size:26px;font-weight:500;color:var(--dark);letter-spacing:.5px}

.sidebar{position:absolute;left:117px;top:159px;width:215px;height:495px;background:var(--white);box-shadow:0 1px 4px rgba(0,0,0,.25)}
.side-head{height:39px;background:var(--blue);color:var(--white);font-size:18px;font-weight:600;padding:10px 17px}
.side-list{list-style:none;padding:8px 0 22px}
.side-list li{height:33px;padding:8px 0 0 31px;font-size:15px;position:relative;color:#555}
.side-list li::before{content:"»";position:absolute;left:19px;top:6px;font-size:13px;color:#333}
.side-list li.current{background:var(--tab)}
.news{padding:13px 18px 14px;border-bottom:1px solid #e4e4e4;font-size:13px;line-height:16.5px}
.news:last-child{border-bottom:0}
.news time{display:block;font-style:italic;font-weight:700;color:#555}

.content{position:absolute;left:357px;top:160px;width:695px}
.hero{height:291px;border:1px solid var(--line);padding:6px;position:relative}
.hero-photo{width:473px;height:278px;background:linear-gradient(90deg,#d9cfc6 0%,#e9e4e0 45%,#eef1f3 80%,#fff 100%)}
.hero-quote{position:absolute;left:460px;top:56px;width:220px;font-size:23.5px;line-height:25px;color:var(--orange)}
.copy{margin-top:29px;font-size:12.8px;line-height:20px}
.copy p+p{margin-top:20px}
a{color:var(--orange);text-decoration:none;font-weight:500}

.tabs{margin-top:35px;border:1px solid #e2e2e2;height:336px}
.tab-bar{display:flex;height:35px}
.tab-bar span{background:var(--tab);font-size:15.5px;font-weight:600;color:#555;padding-top:8px;text-align:center;border-left:1px solid #fff}
.tab-bar .on{background:var(--white);color:var(--blue);border-left:0}
.tab-body{display:flex;gap:12px;padding:24px 0 0 23px}
.tab-photo{flex:none;width:250px;height:249px;border:1px solid var(--line);padding:6px}
.tab-photo div{width:100%;height:100%;background:linear-gradient(135deg,#3b6fa8,#7aa5d6 45%,#a78f6c 70%,#3c5f8d)}
.tab-text{font-size:12.8px;line-height:18.3px;width:395px}
.tab-text p+p{margin-top:18px}

.site-footer{position:absolute;left:0;top:1138px;width:100%;height:62px;background:var(--footer);color:var(--white)}
.foot-nav{position:absolute;left:117px;top:27px;font-size:12.8px}
.social{position:absolute;left:803px;top:21px;display:flex;gap:5px}
.social span{width:24px;height:24px;border-radius:50%;background:var(--white)}
.copyright{position:absolute;left:905px;top:27px;font-size:13.5px}
.copyright em{font-style:normal;color:var(--orange)}
</style>
</head>
<body>
<div class="page">
  <header class="site-header">
    <div class="brand">KVR Inc</div>
    <nav class="main-nav">
      <span>Company</span><span class="active">Products &amp; Services</span><span>Learning Center</span><span>Events</span><span>KVR News</span><span>Contact</span>
    </nav>
    <div class="search">Search
      <svg width="13" height="13" viewBox="0 0 13 13"><circle cx="5" cy="5" r="4" fill="none" stroke="#ccc" stroke-width="1.5"/><line x1="8" y1="8" x2="12" y2="12" stroke="#ccc" stroke-width="1.8"/></svg>
    </div>
  </header>

  <div class="wrap page-title"><h1>PIPETTES</h1></div>

  <aside class="sidebar">
    <div class="side-head">Product Overview</div>
    <ul class="side-list">
      <li>Reagents</li><li class="current">Pipettes</li><li>Tubes</li>
    </ul>
    <div class="side-head">Latest News</div>
    <div class="news"><time>October 7, 2013</time>Lorem ipsum dolor sit &nbsp;amet, consect etureius mod dipisi cing elit, sed do eiusmod tempor mod &gt;&gt;&gt;</div>
    <div class="news"><time>October 7, 2013</time>Lorem ipsum dolor sit &nbsp;amet, consect etureius mod dipisi cing elit, sed do eiusmod tempor mod &gt;&gt;&gt;</div>
  </aside>

  <main class="content">
    <section class="hero">
      <div class="hero-photo" role="img" aria-label="Three scientists in a laboratory looking at a microscope screen"></div>
      <p class="hero-quote">Donec non massa lacinia, commodo eros eget, id rutrum arcu. Integer velit eleifend congue, massa consequat mauris!</p>
    </section>

    <div class="copy">
      <p>Quisque feugiat lacus vitae posuere blandit. Nulla sit amet laoreet felis, id rhoncus nisl. Aenean fringilla quam in nibh egestas, in malesuada tortor accumsan. Donec non massa lacinia, commodo eros eget, rutrum arcu. Integer tincidunt, velit id eleifend congue, odio massa consequat mauris, a scelerisque nulla nulla eu nulla. Cras luctus pulvinar nibh ut viverra. Aenean vestibulum vitae justo non dictum. Mauris ut tellus in dui pretium dictum nec non tortor. Nulla a velit quis dolor interdum scelerisque eu et nisl.</p>
      <p>Donec auctor mollis ligula eget molestie. Aliquam erat volutpat. Curabitur sapien libero, condimentum ac nisl ultricies tincidunt ipsum. Donec in iaculis metus. Mauris eleifend nisi non sapien commodo, hendrerit consectetur. Pellentesque faucibus, purus non dictum lacinia, ante augue pretium neque, vitae egestas dui nisi et enim. ornare Suspendisse nibh vel lacinia rhoncus Donec auctor mollis ligula eget molestie. Pellentesque faucibus, purus non dictum lacinia, ante augue pretium neque, <a>vitae egestas</a> dui nisi et enim. Suspendisse iaculis nibh vel lacinia rhoncus Donec non massa lacinia, commodo eros eget, rutrum arcu. Integer tincidunt, velit id eleifend congue, odio massa consequat mauris, a scelerisque nulla nulla eu nulla. Cras luctus pulvinar nibh ut viverra. Aenean vestibulum vitae justo non dictum.</p>
    </div>

    <section class="tabs">
      <div class="tab-bar">
        <span class="on" style="width:138px">Overview</span><span style="width:139px">Features</span><span style="width:164px">Specifications</span><span style="width:122px">FAQ's</span><span style="width:131px">Manuals</span>
      </div>
      <div class="tab-body">
        <div class="tab-photo"><div role="img" aria-label="Gloved hands pipetting into a test tube"></div></div>
        <div class="tab-text">
          <p>Quisque feugiat lacus vitae posuere blandit. Nulla sit amet laoreet felis, id rhoncus nisl. Aenean fringilla quam in nibh egestas, in malesuada tortor accumsan. Donec non massa lacinia, commodo eros eget, rutrum arcu. Integer tincidunt, velit id eleifend congue, odio massa consequat mauris, a scelerisque nulla nulla eu nulla. Cras luctus pulvinar nibh ut viverra. Aenean vestibulum vitae justo non dictum. Mauris ut tellus in dui pretium dictum nec non tortor. Nulla a velit quis dolor interdum <a>scelerisque</a> eu et nisl.</p>
          <p>Donec auctor mollis ligula eget molestie. Aliquam erat volutpat. Curabitur sapien libero, condimentum ac nisl nec, ultricies tincidunt ipsum. Donec in iaculis metus. Mauris eleifend nisi non sapien commodo, hendrerit ornare lacus consectetur.</p>
        </div>
      </div>
    </section>
  </main>

  <footer class="site-footer">
    <nav class="foot-nav">Company &nbsp;-&nbsp; Products &amp; Services &nbsp;-&nbsp; Learning Center &nbsp;-&nbsp; Events &nbsp;-&nbsp; KVR News &nbsp;-&nbsp; Contact</nav>
    <div class="social" aria-label="Social links"><span></span><span></span><span></span></div>
    <p class="copyright">Copyright © <em>KVR Inc.</em> 2013</p>
  </footer>
</div>
</body>
</html>
```